Copperleaf Roofing Business Card

This is my current business card. But I’d like to make some changes. Somewhere on the card I’d like to list some of the services we offer. Maybe on the back? But I’d still like to keep the red. White and black modern look.

-residential & commercial roofing
-Roof Repairs & Maintenance
-Storm Damage & Insurance Claims specialist
-Christmas Lights and permanent Christmas lights
Fencing. Windows. Gutters. Siding. Sheetrock, painting.

```html
<!DOCTYPE html>
<html lang="en">
<head>
<meta charset="utf-8">
<title>Copperleaf Roofing Business Card</title>
<link href="https://fonts.googleapis.com/css2?family=Michroma&family=Montserrat:wght@400;500;600;700&display=swap" rel="stylesheet">
<style>
  :root {
    --red: #d92c27;
    --black: #050607;
    --white: #ffffff;
    --ink: #111111;
    --stage: #3b3c3e;
  }
  * { box-sizing: border-box; margin: 0; padding: 0; }
  html, body { width: 1200px; height: 1059px; overflow: hidden; }
  body {
    background: var(--stage);
    font-family: "Montserrat", sans-serif;
    position: relative;
  }
  .card {
    position: absolute;
    border-radius: 21px;
    overflow: hidden;
    box-shadow: 0 14px 28px rgba(0,0,0,0.55);
  }
  .card--front { left: 256px; top: 100px; width: 688px; height: 391px; background: var(--white); }
  .card--back  { left: 253px; top: 537px; width: 693px; height: 394px; background: var(--black); }

  /* brand lockup */
  .brand { position: absolute; left: 0; right: 0; text-align: center; }
  .brand__dot { display: block; margin: 0 auto; border-radius: 50%; background: var(--red); }
  .brand__name { font-weight: 700; letter-spacing: 1px; line-height: 1.15; }
  .card--front .brand { top: 56px; }
  .card--front .brand__dot { width: 84px; height: 84px; margin-bottom: 14px; }
  .card--front .brand__name { color: var(--red); font-size: 25px; }
  .card--back .brand { top: 46px; }
  .card--back .brand__dot { width: 130px; height: 130px; border: 3px solid var(--white); margin-bottom: 16px; }
  .card--back .brand__name { color: var(--white); font-size: 22px; }

  /* person */
  .person { position: absolute; right: calc(688px - 319px); top: 276px; text-align: right; }
  .person__name { font-family: "Michroma", sans-serif; font-size: 22px; letter-spacing: 1px; white-space: nowrap; color: var(--ink); font-weight: 400; }
  .person__name .first { color: var(--red); }
  .person__role { color: var(--red); font-size: 15px; font-weight: 500; letter-spacing: 1px; margin-top: 4px; }
  .divider { position: absolute; left: 343px; top: 270px; width: 2px; height: 69px; background: var(--ink); }

  /* contacts */
  .contacts { position: absolute; left: 368px; top: 268px; list-style: none; }
  .contacts li { display: flex; align-items: center; height: 26px; font-size: 15px; font-weight: 500; color: var(--ink); }
  .contacts .phone { letter-spacing: 3px; font-weight: 600; }
  .contacts svg { width: 13px; height: 13px; margin-right: 10px; flex: none; }

  /* bottom band */
  .band { position: absolute; left: 0; right: 0; bottom: 0; height: 16px; background: var(--red); }
  .band__hatch {
    position: absolute; top: 0; height: 16px; width: 120px;
    clip-path: polygon(10px 0, 100% 0, calc(100% - 10px) 100%, 0 100%);
  }
  .card--front .band__hatch { background: repeating-linear-gradient(60deg, var(--ink) 0 4px, var(--white) 4px 8px); }
  .card--back .band__hatch { background: repeating-linear-gradient(60deg, var(--white) 0 4px, var(--black) 4px 8px); }
  .band__hatch--left { left: 84px; }
  .band__hatch--right { left: 490px; }

  /* services */
  .services { position: absolute; left: 29px; right: 28px; top: 266px; color: var(--white); }
  .services__title { display: flex; align-items: center; gap: 16px; font-size: 20px; font-weight: 500; letter-spacing: 0.5px; }
  .services__title::before, .services__title::after { content: ""; flex: 1; height: 1.5px; background: var(--red); }
  .services__row { display: flex; justify-content: space-between; font-size: 15px; margin-top: 10px; white-space: nowrap; }
  .services__row + .services__row { margin-top: 7px; }
  .services__item::before { content: ""; display: inline-block; width: 6px; height: 6px; border-radius: 50%; background: var(--red); margin-right: 8px; vertical-align: middle; position: relative; top: -2px; }
</style>
</head>
<body>

<section class="card card--front">
  <div class="brand">
    <span class="brand__dot"></span>
    <div class="brand__name">COPPERLEAF<br>ROOFING CO.</div>
  </div>

  <div class="person">
    <div class="person__name"><span class="first">DANA</span> MERCER</div>
    <div class="person__role">OWNER</div>
  </div>
  <div class="divider"></div>

  <ul class="contacts">
    <li class="phone">
      <svg viewBox="0 0 16 16"><path fill="#d92c27" d="M3.5 1.5l2.5 0 1 3.5-1.6 1.2a8 8 0 0 0 4.4 4.4L11 9l3.5 1v2.5c0 1-.8 2-2 2A11 11 0 0 1 1.5 3.5c0-1.2 1-2 2-2z"/></svg>
      555-013-4820
    </li>
    <li>
      <svg viewBox="0 0 16 16"><rect x="1" y="3" width="14" height="10" rx="1" fill="#d92c27"/><path d="M1.5 3.8L8 9l6.5-5.2" stroke="#fff" stroke-width="1.3" fill="none"/></svg>
      dana@copperleafroofing.co
    </li>
    <li>
      <svg viewBox="0 0 16 16" fill="none" stroke="#d92c27" stroke-width="1.2"><circle cx="8" cy="8" r="6.5"/><ellipse cx="8" cy="8" rx="3" ry="6.5"/><path d="M1.5 8h13M2.5 5h11M2.5 11h11"/></svg>
      www.copperleafroofing.co
    </li>
  </ul>

  <div class="band">
    <span class="band__hatch band__hatch--left"></span>
    <span class="band__hatch band__hatch--right"></span>
  </div>
</section>

<section class="card card--back">
  <div class="brand">
    <span class="brand__dot"></span>
    <div class="brand__name">COPPERLEAF ROOFING CO.</div>
  </div>

  <div class="services">
    <h2 class="services__title">WE OFFER</h2>
    <div class="services__row">
      <span class="services__item">Residential &amp; commercial roofing</span>
      <span class="services__item">Storm Damage &amp; Insurance Claims specialist</span>
    </div>
    <div class="services__row">
      <span class="services__item">Roof Repairs &amp; Maintenance</span>
      <span class="services__item">Christmas Lights and permanent Christmas lights</span>
    </div>
  </div>

  <div class="band">
    <span class="band__hatch band__hatch--left"></span>
    <span class="band__hatch band__hatch--right"></span>
  </div>
</section>

</body>
</html>
```